Redesign and move to Wordpress for corvandel.com

Our website needs a redesign and at the same time we are moving it to Wordpress. Please help us with a new digital professional look and feel.

We are an Australian Software Engineering company specialising in advanced software development using in A.I., PLatform Engineering, Integration and Cloud. See the current corvandel.com for more information about us.

```html
<!DOCTYPE html>
<html lang="en">
<head>
<meta charset="utf-8">
<title>corvandel — Reliable Smart Software Engineering</title>
<link rel="stylesheet" href="https://fonts.googleapis.com/css2?family=Audiowide&family=Roboto:wght@300;400;500;700&display=swap">
<style>
:root{
  --blue:#1b5fa6;
  --navy:#123a68;
  --deep:#0c2f57;
  --teal:#3fbcb0;
  --teal-dark:#2aa399;
  --ink:#2b2b2b;
  --muted:#6b7280;
  --pale:#e9f3fb;
  --white:#ffffff;
}
*{box-sizing:border-box;margin:0;padding:0}
html,body{width:1200px;height:4218px;overflow:hidden}
body{font-family:"Roboto",Arial,sans-serif;color:var(--ink);background:var(--white);position:relative}
.abs{position:absolute}
.display{font-family:"Audiowide","Roboto",sans-serif;font-weight:400}

/* top bar & header */
.topbar{left:606px;top:0;width:594px;height:30px;background:var(--blue);color:#fff;font-size:13px}
.topbar .social{position:absolute;top:9px;width:12px;height:12px;border-radius:50%;background:#fff;opacity:.9}
.topbar .info{position:absolute;top:7px;display:flex;align-items:center;gap:6px;font-weight:500}
.header{left:0;top:30px;width:1200px;height:70px;background:#fff}
.brand{display:flex;align-items:center;gap:14px}
.brand .mark{width:42px;height:42px;border:4px solid var(--teal)}
.brand .name{font-family:"Roboto",sans-serif;font-weight:300;font-size:38px;color:var(--blue);letter-spacing:2px}
.nav a{position:absolute;top:27px;font-size:15px;font-weight:500;color:var(--ink);text-decoration:none}
.nav a.active{color:var(--teal)}
.btn{display:inline-flex;align-items:center;justify-content:center;gap:8px;border-radius:30px;font-weight:700;text-transform:uppercase;text-decoration:none;font-size:15px;line-height:1}
.btn svg{flex:none;display:block;margin:0}
.demo{left:951px;top:17px;width:138px;height:36px;background:var(--teal);color:#fff;font-size:13px;font-weight:500}

/* hero */
.hero{left:0;top:100px;width:1200px;height:586px;background:radial-gradient(ellipse at 80% 45%,#1c6fc4 0%,#0f4f95 35%,#0b3a6c 70%,#0a2f55 100%)}
.hero-art{position:absolute;left:560px;top:0;width:640px;height:586px;background:radial-gradient(circle at 55% 55%,rgba(90,170,240,.45),rgba(20,80,150,0) 65%)}
.hero h1{position:absolute;left:111px;top:120px;font-size:42px;line-height:53px;color:#fff;letter-spacing:1px}
.hero p{position:absolute;left:111px;top:310px;width:460px;font-size:16px;line-height:27px;color:#fff;font-weight:500}
.hero .btn{position:absolute;left:111px;top:399px;width:198px;height:50px;background:var(--teal);color:#fff;font-size:16px}

/* section titles */
.sec-title{position:absolute;left:0;width:1200px;text-align:center;font-size:36px;color:var(--navy)}
.sec-title .lead{color:var(--blue)}
.sec-title::after{content:"";display:block;width:66px;height:4px;background:var(--teal);margin:14px auto 0}

/* services */
.services{left:0;top:686px;width:1200px;height:624px;background:#fff}
.card{position:absolute;top:193px;width:226px;height:313px;color:#fff;text-align:center;padding:20px 10px}
.card.blue{background:var(--blue)}
.card.teal{background:var(--teal)}
.card.raised{top:170px;height:359px;padding-top:28px;box-shadow:0 10px 24px rgba(0,0,0,.22)}
.card .icon{display:block;margin:0 auto 12px}
.card h3{font-size:17px;line-height:23px;font-weight:500;margin-bottom:10px}
.card p{font-size:12.5px;line-height:20px;font-weight:400;opacity:.95}
.card .btn{position:absolute;left:43px;bottom:22px;width:140px;height:42px;border:2px solid #fff;color:#fff;font-size:14px}
.arrow{position:absolute;top:1010px}

/* about */
.about{left:0;top:1310px;width:1200px;height:582px;background:var(--pale)}
.photo{position:absolute;border:5px solid var(--blue)}
.photo.t{border-color:var(--teal)}
.about h2{position:absolute;left:645px;top:83px;font-size:36px;color:var(--navy)}
.about h2 .lead{color:var(--blue)}
.about h2::after{content:"";display:block;width:66px;height:4px;background:var(--teal);margin-top:10px}
.about p{position:absolute;left:645px;width:444px;font-size:14px;line-height:25px;color:#555;text-align:justify}
.about .btn{position:absolute;left:645px;top:414px;width:174px;height:48px;background:var(--blue);color:#fff;font-size:15px}

/* cta band */
.band{left:0;top:1892px;width:1200px;height:403px;background:linear-gradient(180deg,#1f66b0,#175aa0 60%,#1a62ad)}
.band h2{position:absolute;left:0;top:62px;width:1200px;text-align:center;font-size:36px;line-height:43px;color:#fff}
.band p{position:absolute;left:150px;top:202px;width:900px;text-align:center;font-size:15px;line-height:26px;color:#fff}
.band .btn{position:absolute;left:516px;top:282px;width:173px;height:46px;background:var(--teal);color:#fff}

/* news */
.news{left:0;top:2295px;width:1200px;height:635px;background:#fff}
.post{position:absolute;top:160px;width:311px;height:390px;background:#fff;box-shadow:0 2px 14px rgba(0,0,0,.1);border-radius:6px;text-align:center}
.post .thumb{position:absolute;left:8px;top:8px;width:295px;height:202px;border-radius:4px}
.post .date{position:absolute;left:0;top:238px;width:311px;font-size:13px;color:var(--blue)}
.post h3{position:absolute;left:0;top:260px;width:311px;font-size:17px;font-weight:500;color:var(--ink)}
.post p{position:absolute;left:14px;top:293px;width:283px;font-size:14px;line-height:23px;color:#777}
.post .more{position:absolute;left:0;top:350px;width:311px;font-size:15px;font-weight:500;color:var(--teal);text-transform:uppercase;display:flex;justify-content:center;align-items:center;gap:6px}

/* clients */
.clients{left:0;top:2930px;width:1200px;height:332px;background:var(--pale)}
.client{position:absolute;top:160px;width:233px;height:87px;background:#fff;display:flex;align-items:center;justify-content:center;gap:8px;font-size:30px;font-weight:700;color:#333}

/* consult */
.consult{left:0;top:3262px;width:1200px;height:568px;background:linear-gradient(100deg,#1a5aa3 0%,#1f6db0 45%,#2f9cb5 80%,#3fbcb0 100%)}
.consult .sec-title{color:#fff}
.consult .sec-title .lead{color:#fff}
.field{position:absolute;background:#fff;border:1px solid #cfd8e3;font-size:14px;color:#666;padding:12px 16px}
.consult .btn{position:absolute;left:524px;top:446px;width:154px;height:42px;border:2px solid #fff;color:#fff;font-size:15px;background:rgba(255,255,255,.08)}

/* footer */
.footer{left:0;top:3830px;width:1200px;height:330px;background:#fff}
.footer h4{position:absolute;top:68px;font-size:18px;font-weight:700;color:var(--ink)}
.footer h4::after{content:"";display:block;width:54px;height:3px;background:var(--blue);margin-top:8px}
.flinks a{position:absolute;left:438px;font-size:12px;color:#444;text-decoration:none}
.fcontact{position:absolute;left:612px;display:flex;align-items:center;gap:12px;font-size:12px;color:#444}
.fcontact .ic{width:24px;height:24px;border-radius:50%;background:var(--blue);display:flex;align-items:center;justify-content:center}
.sub-text{position:absolute;left:836px;top:128px;width:250px;font-size:12px;line-height:21px;color:#444}
.sub-input{position:absolute;left:837px;top:177px;width:252px;height:35px;border-radius:20px;background:#eef3f8;font-size:11px;color:#777;display:flex;align-items:center;padding-left:14px;gap:6px}
.sub-input .go{position:absolute;right:0;top:0;width:48px;height:35px;border-radius:20px;background:var(--teal);display:flex;align-items:center;justify-content:center}
.fsocial{position:absolute;top:240px;width:18px;height:18px;border-radius:50%;background:var(--ink)}
.fsocial.on{background:var(--teal);width:28px;height:28px;top:235px}
.bottom{left:0;top:4160px;width:1200px;height:58px;background:var(--pale);font-size:13px;color:#555}
.bottom span{position:absolute;top:21px}
</style>
</head>
<body>

<div class="abs topbar">
  <span class="social" style="left:28px"></span>
  <span class="social" style="left:50px"></span>
  <span class="social" style="left:72px"></span>
  <span class="social" style="left:96px"></span>
  <span class="info" style="left:184px">
    <svg width="10" height="13" viewBox="0 0 10 13"><path d="M5 0a5 5 0 0 0-5 5c0 3.5 5 8 5 8s5-4.5 5-8a5 5 0 0 0-5-5zm0 7a2 2 0 1 1 0-4 2 2 0 0 1 0 4z" fill="#fff"/></svg>48 Harbour Lane</span>
  <span class="info" style="left:378px">
    <svg width="12" height="12" viewBox="0 0 12 12"><path d="M2.5 0l2 3-1.3 1.3a7 7 0 0 0 4.5 4.5L9 7.5l3 2-1 2.5C5 12 0 7 0 1z" fill="#fff"/></svg>555-014-2290</span>
</div>

<header class="abs header">
  <div class="abs brand" style="left:111px;top:0;height:52px">
    <span class="mark"></span><span class="name">corvandel</span>
  </div>
  <nav class="nav">
    <a class="active" style="left:466px">Home</a>
    <a style="left:539px">About Us</a>
    <a style="left:632px">Our Services</a>
    <a style="left:750px">News</a>
    <a style="left:819px">Contact</a>
    <svg class="abs" style="left:903px;top:29px" width="16" height="16" viewBox="0 0 16 16"><circle cx="6.5" cy="6.5" r="5" fill="none" stroke="#2b2b2b" stroke-width="2.2"/><path d="M10.5 10.5l4 4" stroke="#2b2b2b" stroke-width="2.4"/></svg>
  </nav>
  <a class="abs btn demo">Request Demo</a>
</header>

<section class="abs hero">
  <div class="hero-art" role="img" aria-label="Glowing digital globe made of connected network points"></div>
  <h1 class="display">Reliable Smart<br>Software<br>Engineering</h1>
  <p>At Corvandel, we craft bespoke software solutions that are not available on the market.</p>
  <a class="btn">Get Started
    <svg width="15" height="15" viewBox="0 0 16 16"><circle cx="8" cy="8" r="8" fill="#fff"/><path d="M6.5 4.5L10 8l-3.5 3.5" stroke="#3fbcb0" stroke-width="2" fill="none"/></svg></a>
</section>

<section class="abs services">
  <h2 class="sec-title display" style="top:60px"><span class="lead">Our</span> Services</h2>

  <div class="card blue" style="left:111px">
    <svg class="icon" width="40" height="40" viewBox="0 0 46 46" fill="none" stroke="#fff" stroke-width="2"><rect x="6" y="6" width="18" height="22" rx="2"/><circle cx="30" cy="30" r="9"/><circle cx="30" cy="30" r="3"/><path d="M10 12h10M10 17h10M10 22h6"/></svg>
    <h3>Enterprise Systems Integration</h3>
    <p>Automate your business processes internally or externally to improve data quality and process efficiency</p>
    <a class="btn">Read More <svg width="13" height="13" viewBox="0 0 16 16"><circle cx="8" cy="8" r="8" fill="#fff"/><path d="M6.5 4.5L10 8l-3.5 3.5" stroke="#1b5fa6" stroke-width="2" fill="none"/></svg></a>
  </div>

  <div class="card teal raised" style="left:362px">
    <svg class="icon" width="60" height="60" viewBox="0 0 60 60" fill="none" stroke="#fff" stroke-width="2"><circle cx="30" cy="30" r="7"/><circle cx="30" cy="8" r="4"/><circle cx="30" cy="52" r="4"/><circle cx="10" cy="19" r="4"/><circle cx="50" cy="19" r="4"/><circle cx="10" cy="41" r="4"/><circle cx="50" cy="41" r="4"/><path d="M30 12v11M30 37v11M14 21l10 5M46 21l-10 5M14 39l10-5M46 39l-10-5"/></svg>
    <h3>Microservices</h3>
    <p>Leverage Microservices Architecture to enable quick deployment, dynamically scalable service performance, team productivity and more</p>
    <a class="btn">Read More <svg width="13" height="13" viewBox="0 0 16 16"><circle cx="8" cy="8" r="8" fill="#fff"/><path d="M6.5 4.5L10 8l-3.5 3.5" stroke="#3fbcb0" stroke-width="2" fill="none"/></svg></a>
  </div>

  <div class="card blue" style="left:612px">
    <svg class="icon" width="44" height="44" viewBox="0 0 52 52" fill="none" stroke="#fff" stroke-width="2"><circle cx="26" cy="26" r="22" stroke-dasharray="4 3"/><circle cx="26" cy="26" r="14"/><circle cx="26" cy="26" r="5"/></svg>
    <h3>Platform Engineering</h3>
    <p>For organisations looking to manage the security and cost risks around their cloud infrastructure management for applications</p>
    <a class="btn">Read More <svg width="13" height="13" viewBox="0 0 16 16"><circle cx="8" cy="8" r="8" fill="#fff"/><path d="M6.5 4.5L10 8l-3.5 3.5" stroke="#1b5fa6" stroke-width="2" fill="none"/></svg></a>
  </div>

  <div class="card teal" style="left:863px">
    <svg class="icon" width="44" height="44" viewBox="0 0 52 52" fill="none" stroke="#fff" stroke-width="2"><rect x="12" y="12" width="28" height="28" rx="3"/><rect x="19" y="19" width="14" height="14"/><path d="M18 4v8M26 4v8M34 4v8M18 40v8M26 40v8M34 40v8M4 18h8M4 26h8M4 34h8M40 18h8M40 26h8M40 34h8"/></svg>
    <h3>Conversational AI</h3>
    <p>Enabling legacy systems with conversational user interfaces, or simply building intelligent natural language based services, conversational AI has many use cases</p>
    <a class="btn">Read More <svg width="13" height="13" viewBox="0 0 16 16"><circle cx="8" cy="8" r="8" fill="#fff"/><path d="M6.5 4.5L10 8l-3.5 3.5" stroke="#3fbcb0" stroke-width="2" fill="none"/></svg></a>
  </div>
</section>
<svg class="arrow" style="left:38px" width="24" height="40" viewBox="0 0 24 40"><path d="M20 3L4 20l16 17" stroke="#9aa3ad" stroke-width="4" fill="none"/></svg>
<svg class="arrow" style="left:1134px" width="24" height="40" viewBox="0 0 24 40"><path d="M4 3l16 17L4 37" stroke="#9aa3ad" stroke-width="4" fill="none"/></svg>

<section class="abs about">
  <div class="photo" style="left:110px;top:63px;width:219px;height:146px;background:linear-gradient(135deg,#2c4f6a,#7ea3b8)" role="img" aria-label="Developer working behind glowing data screens"></div>
  <div class="photo t" style="left:110px;top:227px;width:219px;height:260px;background:linear-gradient(135deg,#27486b,#6f8fa8 60%,#c9d6df)" role="img" aria-label="Engineer typing on a keyboard at his desk"></div>
  <div class="photo" style="left:349px;top:63px;width:217px;height:261px;background:linear-gradient(160deg,#1f2d3a,#6b5a48 60%,#b98e62)" role="img" aria-label="Hand touching a software development life cycle diagram"></div>
  <div class="photo t" style="left:349px;top:343px;width:217px;height:144px;background:linear-gradient(135deg,#0e3a5e,#2a7fb0)" role="img" aria-label="Hand tapping an AI interface above a laptop"></div>
  <h2 class="display"><span class="lead">About</span> Us</h2>
  <p style="top:173px">At Corvandel, we craft bespoke software solutions that are not available on the market. By building organizations market-leading products, process automation, legacy system enablement, or advanced intelligent systems, we empower our customers to achieve a competitive edge in their industry.</p>
  <p style="top:307px">We have been on a mission to make complex custom enterprise integration accessible to any organisation, regardless of industry, size, or location.</p>
  <a class="btn">Learn More</a>
</section>

<section class="abs band">
  <h2 class="display">Australia's Largest health charity<br>implements</h2>
  <p>By building organizations market-leading products, process automation, legacy system enablement, or advanced intelligent systems, we empower our customers to achieve a competitive edge in their industry.</p>
  <a class="btn">Get Started</a>
</section>

<section class="abs news">
  <h2 class="sec-title display" style="top:65px"><span class="lead">News</span> &amp; Articles</h2>
  <article class="post" style="left:110px">
    <div class="thumb" style="background:linear-gradient(135deg,#3a3f47,#9aa2ab 60%,#d8dde2)" role="img" aria-label="Hands typing on a backlit keyboard"></div>
    <div class="date">&#9635; January 22, 2024</div>
    <h3>Ai In Software Engineering</h3>
    <p>Writing code is more than just writing code. There's commit messages to write,</p>
    <div class="more">Read More <svg width="13" height="13" viewBox="0 0 16 16"><circle cx="8" cy="8" r="8" fill="#3fbcb0"/><path d="M6.5 4.5L10 8l-3.5 3.5" stroke="#fff" stroke-width="2" fill="none"/></svg></div>
  </article>
  <article class="post" style="left:445px">
    <div class="thumb" style="background:linear-gradient(135deg,#0d3a66,#2e7dc0 55%,#8cc3ea)" role="img" aria-label="Hands at a laptop surrounded by holographic data"></div>
    <div class="date">&#9635; January 22, 2024</div>
    <h3>Ai In Software Engineering</h3>
    <p>Writing code is more than just writing code. There's commit messages to write,</p>
    <div class="more">Read More <svg width="13" height="13" viewBox="0 0 16 16"><circle cx="8" cy="8" r="8" fill="#3fbcb0"/><path d="M6.5 4.5L10 8l-3.5 3.5" stroke="#fff" stroke-width="2" fill="none"/></svg></div>
  </article>
  <article class="post" style="left:779px">
    <div class="thumb" style="background:linear-gradient(135deg,#0b2a4c,#1f5f9a 55%,#6fb0dd)" role="img" aria-label="Developer in front of blue data visualisations"></div>
    <div class="date">&#9635; January 22, 2024</div>
    <h3>Ai In Software Engineering</h3>
    <p>Writing code is more than just writing code. There's commit messages to write,</p>
    <div class="more">Read More <svg width="13" height="13" viewBox="0 0 16 16"><circle cx="8" cy="8" r="8" fill="#3fbcb0"/><path d="M6.5 4.5L10 8l-3.5 3.5" stroke="#fff" stroke-width="2" fill="none"/></svg></div>
  </article>
</section>

<section class="abs clients">
  <h2 class="sec-title display" style="top:56px"><span class="lead">Our</span> Clients</h2>
  <div class="client" style="left:111px">NORVA</div>
  <div class="client" style="left:358px"><span style="width:22px;height:22px;background:#333;display:inline-block"></span>Brightfold</div>
  <div class="client" style="left:607px">KESTREL</div>
  <div class="client" style="left:855px"><span style="width:18px;height:18px;border-radius:50%;background:#333;display:inline-block"></span>solvane</div>
</section>

<section class="abs consult">
  <h2 class="sec-title display" style="top:73px">Book A free consultation</h2>
  <div class="field" style="left:188px;top:187px;width:400px;height:43px">Name</div>
  <div class="field" style="left:611px;top:187px;width:401px;height:43px">Email</div>
  <div class="field" style="left:188px;top:253px;width:400px;height:42px">Phone</div>
  <div class="field" style="left:611px;top:253px;width:401px;height:42px">Subjects</div>
  <div class="field" style="left:188px;top:318px;width:824px;height:82px">Message</div>
  <a class="btn">Submit Now</a>
</section>

<footer class="abs footer">
  <div class="abs brand" style="left:110px;top:145px">
    <span class="mark"></span><span class="name">corvandel</span>
  </div>

  <h4 style="left:432px">QUICK LINKS</h4>
  <div class="flinks">
    <a style="top:128px">Home</a>
    <a style="top:154px">About Us</a>
    <a style="top:180px">Our Services</a>
    <a style="top:206px">News</a>
    <a style="top:232px">Contact</a>
  </div>

  <h4 style="left:612px">CONTACT US</h4>
  <div class="fcontact" style="top:126px"><span class="ic"><svg width="11" height="11" viewBox="0 0 12 12"><path d="M2.5 0l2 3-1.3 1.3a7 7 0 0 0 4.5 4.5L9 7.5l3 2-1 2.5C5 12 0 7 0 1z" fill="#fff"/></svg></span>1800 555 019</div>
  <div class="fcontact" style="top:166px"><span class="ic"><svg width="12" height="9" viewBox="0 0 12 9"><rect x=".5" y=".5" width="11" height="8" fill="none" stroke="#fff"/><path d="M.5.5L6 5l5.5-4.5" fill="none" stroke="#fff"/></svg></span>info@corvandel.com</div>
  <div class="fcontact" style="top:205px"><span class="ic"><svg width="9" height="12" viewBox="0 0 10 13"><path d="M5 0a5 5 0 0 0-5 5c0 3.5 5 8 5 8s5-4.5 5-8a5 5 0 0 0-5-5zm0 7a2 2 0 1 1 0-4 2 2 0 0 1 0 4z" fill="#fff"/></svg></span>48 Harbour Lane</div>

  <h4 style="left:830px">SUBSCRIBE TO OUR BLOG</h4>
  <p class="sub-text">Sign up today to get resources on how to attract and retain more customers!</p>
  <div class="sub-input">&#9993; Email Address
    <span class="go"><svg width="16" height="16" viewBox="0 0 16 16"><path d="M1 7l14-6-5 14-2-6z" fill="#fff"/></svg></span></div>
  <span class="fsocial" style="left:838px"></span>
  <span class="fsocial on" style="left:872px"></span>
  <span class="fsocial" style="left:916px"></span>
  <span class="fsocial" style="left:955px"></span>
</footer>

<div class="abs bottom">
  <span style="left:110px">Copyright© 2024 <u>corvandel</u> | All Rights Reserved</span>
  <span style="left:843px">Terms and Conditions &nbsp;|</span>
  <span style="left:1003px">Privacy Policy</span>
</div>

</body>
</html>
```